Vernac Law Business cards and stationary design project

We are looking for a stationary design for business cards (double sided), 8x10, 5x7, and legal and standard envelopes.

We would like the design to match the logo that we have already.
Color palate preferred is Teal, White, grey and any others that will look good for a professional law firm.

We would like this statement: "RELATIONSHIPS. RESPECT. RESULT" to be on the back of the business cards and maybe on the stationary if it looks good.

Please see link to website for more information: www.vernac-law.example

Target Market(s)

Potential clients that need Attorney services.

Industry/Entity Type

Law Firm

Contact Information for Business Card

We would like the front and back to be two different colors. Current business cards are teal front, grey back and are a vertical design. We are open to options with colors.

Font styles to use
Serif

Colors
33a6d7
33b8a4
b9b9b9
5c5c5c

Requirements
Must have
• Logo supplied needs to go on the card and stationary.
• Match website color palate, www.vernac-law.example
• Be professional and not too wordy.
• Criminal Law, Civil Litigation, Personal Injury, Restraining Orders need to be on the card.
Nice to have
• RELATIONSHIPS. RESPECT. RESULTS. on the back of the card.
Should not have
• Not be too busy/wordy or too flashy.

```html
<!DOCTYPE html>
<html lang="en">
<head>
<meta charset="utf-8">
<title>Vernac Law Business Cards</title>
<link rel="stylesheet" href="https://fonts.googleapis.com/css2?family=PT+Sans:wght@400;700&display=swap">
<style>
  :root {
    --backdrop: #2f2b29;
    --card: #050505;
    --card-glow: #1c1c1c;
    --teal: #11909f;
    --white: #ffffff;
  }
  * { margin: 0; padding: 0; box-sizing: border-box; }
  html, body { width: 1200px; height: 844px; overflow: hidden; }
  body {
    background: var(--backdrop);
    font-family: "PT Sans", Arial, sans-serif;
    position: relative;
  }
  .card {
    position: absolute;
    top: 280px;
    width: 520px;
    height: 297px;
    background: radial-gradient(ellipse at 65% 30%, var(--card-glow), var(--card) 70%);
    box-shadow: 0 14px 30px rgba(0,0,0,0.55);
    overflow: hidden;
  }
  .card--front { left: 50px; }
  .card--back { left: 630px; }

  /* Front: contact side */
  .band { position: absolute; left: 0; width: 100%; height: 13px; background: var(--teal); }
  .band--top { top: 0; }
  .band--bottom { bottom: 0; }
  .person {
    position: absolute; top: 68px; left: 0; width: 100%;
    text-align: center;
  }
  .person__name {
    display: inline-block;
    color: var(--teal); font-weight: 700; font-size: 17px;
    letter-spacing: 0.5px; padding: 0 4px 2px;
    border-bottom: 1px solid var(--teal);
  }
  .person__title { color: var(--white); font-size: 14px; margin-top: 2px; }
  .contact {
    position: absolute; top: 150px; left: 0; width: 100%;
    text-align: center; color: var(--white); font-size: 14px; line-height: 18px;
  }
  .contact__address { margin-top: 12px; font-size: 15px; }

  /* Back: brand side */
  .marker { position: absolute; width: 22px; height: 38px; background: var(--teal); }
  .marker--right { top: 20px; right: 0; }
  .marker--left { top: 130px; left: 0; }
  .brand {
    position: absolute; top: 70px; left: 0; width: 100%;
    text-align: center;
  }
  .brand__name {
    color: var(--teal); font-size: 32px; letter-spacing: 4px; text-transform: uppercase;
  }
  .brand__rule { width: 200px; height: 1px; background: var(--teal); margin: 6px auto 0; }
  .practice {
    position: absolute; top: 150px; left: 0; width: 100%;
    text-align: center; color: var(--teal); font-size: 13px; line-height: 17px;
  }
  .tagline {
    position: absolute; top: 200px; left: 40px; right: 40px;
    display: flex; align-items: center; gap: 10px;
    color: var(--teal); font-size: 12.5px; white-space: nowrap;
  }
  .tagline::before, .tagline::after {
    content: ""; flex: 1; height: 1px; background: var(--teal);
  }
  .base-rule { position: absolute; left: 30px; right: 30px; bottom: 34px; height: 2px; background: var(--teal); }
</style>
</head>
<body>
  <section class="card card--front" aria-label="Business card front">
    <div class="band band--top"></div>
    <div class="person">
      <div class="person__name">ADRIAN CALLOWAY</div>
      <div class="person__title">Managing Director</div>
    </div>
    <div class="contact">
      <div>044-456-7890</div>
      <div>123-456-7890</div>
      <div>infoname@yourwebsite.com</div>
      <div>www.website.com</div>
      <div class="contact__address">1234 Address Tag Line | Country Name, AB | 123456</div>
    </div>
    <div class="band band--bottom"></div>
  </section>

  <section class="card card--back" aria-label="Business card back">
    <div class="marker marker--right"></div>
    <div class="marker marker--left"></div>
    <div class="brand">
      <div class="brand__name">Vernac Law</div>
      <div class="brand__rule"></div>
    </div>
    <div class="practice">
      <div>Practice areas, Criminal Law</div>
      <div>Civil Litigation/Personal Injury, Restraining Orders</div>
    </div>
    <div class="tagline">RELATIONSHIPS. RESPECT. RESULT</div>
    <div class="base-rule"></div>
  </section>
</body>
</html>
```